Business Card Design

New business card design

Target Market(s)

Residential & Commercial Property Managers

Industry/Entity Type

Plumbing Services

Contact Information for Business Card

Name - Rowan Keddle, title - Director, Phone Number - 0431 286 517, email - rowan@tbk-plumbing.com.au, Company ABN - 73 215 904 386,

Font styles to use
Sans Serif

Colors
0054AA
0677BA
7BADD7
CADEEF
E8F1F8

```html
<!DOCTYPE html>
<html lang="en">
<head>
<meta charset="utf-8">
<title>TBK Plumbing Services – Business Card</title>
<link rel="stylesheet" href="https://fonts.googleapis.com/css2?family=Montserrat:wght@400;500;700&display=swap">
<style>
  :root {
    --backdrop: #2b2e33;
    --card-dark: #1c2128;
    --card-light: #ffffff;
    --accent-blue: #29a8e0;
    --text-light: #ffffff;
    --text-dark: #1c2128;
  }
  * { box-sizing: border-box; margin: 0; padding: 0; }
  html, body {
    width: 1200px;
    height: 880px;
    overflow: hidden;
    background: var(--backdrop);
    font-family: "Montserrat", Arial, sans-serif;
  }
  .canvas {
    position: relative;
    width: 1200px;
    height: 880px;
  }
  .card {
    position: absolute;
    width: 600px;
    height: 343px;
    border-radius: 26px;
    overflow: hidden;
    box-shadow: 0 18px 40px rgba(0, 0, 0, 0.45);
  }
  .card--front {
    left: 60px;
    top: 80px;
    background: var(--card-dark);
    display: flex;
    align-items: center;
    justify-content: center;
  }
  .brand-name {
    font-weight: 500;
    letter-spacing: 0.02em;
  }
  .card--front .brand-name {
    color: var(--text-light);
    font-size: 40px;
  }
  .card--back {
    left: 540px;
    top: 457px;
    background: var(--card-dark);
  }
  .card-swoosh {
    position: absolute;
    inset: 0;
    width: 100%;
    height: 100%;
  }
  .card--back .brand-name {
    position: absolute;
    right: 36px;
    top: 62px;
    color: var(--text-dark);
    font-size: 26px;
  }
  .contact-block {
    position: absolute;
    left: 0;
    bottom: 26px;
    padding-left: 46px;
    color: var(--text-light);
  }
  .contact-block::before {
    content: "";
    position: absolute;
    left: 0;
    top: 4px;
    width: 26px;
    height: 52px;
    background: var(--accent-blue);
  }
  .holder-name {
    color: var(--accent-blue);
    font-weight: 700;
    font-size: 26px;
    line-height: 1.1;
  }
  .holder-title {
    font-size: 17px;
    line-height: 1.3;
    margin-bottom: 14px;
  }
  .company-abn {
    font-size: 16px;
    line-height: 1.3;
    margin-bottom: 12px;
  }
  .contact-line {
    display: flex;
    align-items: center;
    gap: 8px;
    font-size: 16px;
    line-height: 1.45;
  }
  .contact-icon {
    width: 16px;
    height: 16px;
    flex: none;
  }
</style>
</head>
<body>
<main class="canvas">

  <section class="card card--front" aria-label="Business card front">
    <span class="brand-name">TBK Plumbing Services</span>
  </section>

  <section class="card card--back" aria-label="Business card back">
    <svg class="card-swoosh" viewBox="0 0 600 343" aria-hidden="true">
      <path d="M140,0 Q340,280 600,194 L600,0 Z" fill="var(--card-light)"/>
      <path d="M170,0 Q340,250 600,185 L600,191 Q340,270 150,0 Z" fill="var(--accent-blue)"/>
    </svg>

    <span class="brand-name">TBK Plumbing Services</span>

    <div class="contact-block">
      <p class="holder-name">Rowan Keddle</p>
      <p class="holder-title">Director</p>
      <p class="company-abn">Company ABN<br>- 73 215 904 386</p>
      <p class="contact-line">
        <svg class="contact-icon" viewBox="0 0 24 24" aria-hidden="true">
          <path fill="var(--accent-blue)" d="M6.6 10.8a15.1 15.1 0 0 0 6.6 6.6l2.2-2.2a1 1 0 0 1 1-.25 11.4 11.4 0 0 0 3.6.57 1 1 0 0 1 1 1V20a1 1 0 0 1-1 1A17 17 0 0 1 3 4a1 1 0 0 1 1-1h3.5a1 1 0 0 1 1 1c0 1.25.2 2.45.57 3.57a1 1 0 0 1-.25 1z"/>
        </svg>
        0431 286 517
      </p>
      <p class="contact-line">
        <svg class="contact-icon" viewBox="0 0 24 24" aria-hidden="true">
          <path fill="var(--accent-blue)" d="M3 5h18a1 1 0 0 1 1 1v12a1 1 0 0 1-1 1H3a1 1 0 0 1-1-1V6a1 1 0 0 1 1-1zm1 2.3V17h16V7.3l-8 5.2z M5 7l7 4.6L19 7z"/>
        </svg>
        rowan@tbk-plumbing.com.au
      </p>
    </div>
  </section>

</main>
</body>
</html>
```